KLV Plant Services

We are a heavy diesel mechanical business with additional air con certificates, remapping engine rebuilt

Contact Information for Business Card

Company Name, Director Name, Managing Director, Contact details, email and website

Font styles to use
Serif
Script

```html
<!DOCTYPE html>
<html lang="en">
<head>
<meta charset="utf-8">
<title>KLV Plant Services – Business Card</title>
<link rel="stylesheet" href="https://fonts.googleapis.com/css2?family=Arimo:wght@400;700&display=swap">
<style>
  :root {
    --page-bg: #d9d5cf;
    --card-bg: #ebe8e4;
    --card-edge: #c9c4bd;
    --navy: #1c1a45;
    --ink: #1f1f24;
    --muted: #55545a;
    --rule: #2a2a30;
  }
  html, body {
    margin: 0;
    padding: 0;
    width: 1170px;
    height: 1200px;
    overflow: hidden;
    background: var(--page-bg);
    font-family: "Arimo", Arial, sans-serif;
  }
  .canvas {
    position: relative;
    width: 1170px;
    height: 1200px;
  }
  .card {
    position: absolute;
    left: 85px;
    top: 315px;
    width: 1000px;
    height: 569px;
    background: var(--card-bg);
    border: 2px solid var(--card-edge);
    border-radius: 26px;
    box-sizing: border-box;
    box-shadow: 0 10px 30px rgba(0,0,0,0.12);
  }
  .brand {
    position: absolute;
    left: 65px;
    top: 150px;
    display: flex;
    align-items: center;
    gap: 16px;
  }
  .brand-dot {
    width: 34px;
    height: 34px;
    border-radius: 50%;
    background: var(--navy);
  }
  .brand-name {
    font-weight: 700;
    font-size: 40px;
    color: var(--navy);
    letter-spacing: 0.2px;
  }
  .person {
    position: absolute;
    right: 65px;
    top: 326px;
    text-align: right;
  }
  .person-name {
    margin: 0;
    font-weight: 700;
    font-size: 37px;
    line-height: 40px;
    color: var(--navy);
  }
  .person-title {
    margin: 0;
    font-size: 25px;
    line-height: 30px;
    color: var(--ink);
  }
  .divider {
    position: absolute;
    left: 65px;
    right: 65px;
    top: 401px;
    height: 0;
    border-top: 1.5px solid var(--rule);
  }
  .address {
    position: absolute;
    left: 65px;
    top: 426px;
    font-size: 25px;
    line-height: 31px;
    color: var(--muted);
    font-style: normal;
  }
  .contacts {
    position: absolute;
    right: 65px;
    top: 424px;
    margin: 0;
    padding: 0;
    list-style: none;
    text-align: right;
  }
  .contacts li {
    display: flex;
    justify-content: flex-end;
    align-items: center;
    gap: 7px;
    font-size: 25px;
    line-height: 31.5px;
    color: var(--ink);
  }
  .contacts svg {
    width: 20px;
    height: 20px;
    fill: var(--navy);
  }
</style>
</head>
<body>
<main class="canvas">
  <section class="card" aria-label="KLV Plant Services business card">
    <div class="brand">
      <span class="brand-dot" aria-hidden="true"></span>
      <span class="brand-name">KLV Plant Services</span>
    </div>

    <div class="person">
      <p class="person-name">Owen Hartley</p>
      <p class="person-title">Managing Director</p>
    </div>

    <div class="divider"></div>

    <address class="address">
      2170 Harbor Lane<br>
      Maple Grove, NY 11020
    </address>

    <ul class="contacts">
      <li>(555) 0142-7781
        <svg viewBox="0 0 24 24" aria-hidden="true"><path d="M6.6 10.8a15.1 15.1 0 0 0 6.6 6.6l2.2-2.2a1 1 0 0 1 1-.25 11.4 11.4 0 0 0 3.6.57 1 1 0 0 1 1 1V20a1 1 0 0 1-1 1A17 17 0 0 1 3 4a1 1 0 0 1 1-1h3.5a1 1 0 0 1 1 1c0 1.25.2 2.45.57 3.57a1 1 0 0 1-.25 1z"/></svg>
      </li>
      <li>name@KLV.com
        <svg viewBox="0 0 24 24" aria-hidden="true"><path d="M2 5h20v14H2z" opacity="0.9"/><path d="M2 5l10 8 10-8" fill="none" stroke="#ebe8e4" stroke-width="1.8"/></svg>
      </li>
      <li>www.KLV.com
        <svg viewBox="0 0 24 24" aria-hidden="true"><circle cx="12" cy="12" r="10"/><path d="M12 2a10 10 0 0 1 0 20M2 12h20M12 2c-3 3-3 17 0 20" fill="none" stroke="#ebe8e4" stroke-width="1.5"/></svg>
      </li>
    </ul>
  </section>
</main>
</body>
</html>
```